Ridgeline Journeys business card

please see website
www.ridgelinejourneys.comau

info needed on card
Curtis Halvey
Ph
email
Adventure Riding GPS trails

please use my logo and colours off my site

Curtis Halvey
curtis@ridgelinejourneys.com

```html
<!DOCTYPE html>
<html lang="en">
<head>
<meta charset="utf-8">
<title>Ridgeline Journeys business card</title>
<link href="https://fonts.googleapis.com/css2?family=Open+Sans:ital,wght@0,400;0,600;0,700;1,400;1,600&display=swap" rel="stylesheet">
<style>
  :root {
    --backdrop: #4a4a4a;
    --card-white: #f7f7f7;
    --card-black: #000000;
    --ink: #1a1a1a;
    --ink-soft: #444444;
    --rule: #8a8a8a;
    --accent: #f6d80f;
    --accent-deep: #f2c200;
  }
  * { box-sizing: border-box; margin: 0; padding: 0; }
  html, body { width: 1200px; height: 750px; overflow: hidden; }
  body {
    background: var(--backdrop);
    font-family: "Open Sans", Arial, sans-serif;
    position: relative;
  }
  .card {
    position: absolute;
    left: 371px;
    width: 461px;
    height: 262px;
    overflow: hidden;
  }
  .card-front { top: 99px; background: var(--card-white); }
  .card-back { top: 381px; background: var(--card-black); }

  .brand {
    position: absolute;
    left: 26px;
    top: 44px;
    display: flex;
    align-items: center;
    gap: 12px;
  }
  .brand-dot {
    width: 30px; height: 30px;
    border-radius: 50%;
    background: var(--accent);
  }
  .brand-name {
    font-weight: 700;
    font-size: 19px;
    color: var(--ink);
    letter-spacing: 0.2px;
  }

  .holder-name {
    position: absolute;
    right: 24px;
    top: 142px;
    font-weight: 600;
    font-size: 16px;
    color: var(--ink);
  }
  .holder-tab {
    position: absolute;
    left: 453px;
    top: 144px;
    width: 8px;
    height: 27px;
    background: var(--accent);
  }
  .name-rule {
    position: absolute;
    left: 24px;
    top: 168px;
    width: 388px;
    height: 1px;
    background: var(--rule);
  }
  .contact-list {
    position: absolute;
    left: 24px;
    top: 179px;
    list-style: none;
  }
  .contact-list li {
    display: flex;
    align-items: center;
    gap: 6px;
    height: 18.5px;
    font-size: 10.5px;
    color: var(--ink-soft);
  }
  .contact-list svg { width: 11px; height: 11px; flex: none; }
  .tagline {
    position: absolute;
    right: 24px;
    top: 216px;
    font-style: italic;
    font-weight: 600;
    font-size: 12px;
    color: var(--ink-soft);
  }
  .footer-band {
    position: absolute;
    left: 0; bottom: 0;
    width: 461px; height: 11px;
  }

  .back-brand {
    position: absolute;
    left: 0; right: 0;
    top: 90px;
    display: flex;
    flex-direction: column;
    align-items: center;
    gap: 12px;
  }
  .back-brand .brand-dot { width: 44px; height: 44px; }
  .back-brand .brand-name { color: #ffffff; font-size: 20px; }
  .back-url {
    position: absolute;
    left: 0; right: 0;
    top: 216px;
    text-align: center;
    font-style: italic;
    font-size: 11px;
    color: var(--accent);
  }
</style>
</head>
<body>
  <section class="card card-front">
    <div class="brand">
      <span class="brand-dot"></span>
      <span class="brand-name">Ridgeline Journeys</span>
    </div>

    <div class="holder-name">Curtis Halvey</div>
    <div class="holder-tab"></div>
    <div class="name-rule"></div>

    <ul class="contact-list">
      <li>
        <svg viewBox="0 0 16 16" aria-hidden="true"><path fill="#111" d="M3.6 1.2l2.3 2.6-1.4 1.9c.9 2.2 2.6 3.9 4.8 4.8l1.9-1.4 2.6 2.3-1.3 2.4C7.6 13.6 2.4 8.4 1.2 3.1z"/></svg>
        <span>612 584 9073</span>
      </li>
      <li>
        <svg viewBox="0 0 16 16" aria-hidden="true"><rect x="1" y="3" width="14" height="10" fill="#111"/><path d="M1.5 3.5L8 9l6.5-5.5" fill="none" stroke="#fff" stroke-width="1.3"/></svg>
        <span>curtis@ridgelinejourneys.com</span>
      </li>
      <li>
        <svg viewBox="0 0 16 16" aria-hidden="true"><circle cx="8" cy="8" r="7" fill="#111"/><path d="M1 8h14M8 1c-3 3-3 11 0 14M8 1c3 3 3 11 0 14" fill="none" stroke="#fff" stroke-width="1"/></svg>
        <span>www.ridgelinejourneys.com.au</span>
      </li>
    </ul>

    <div class="tagline">Adventure Riding GPS trails</div>

    <svg class="footer-band" viewBox="0 0 461 11" preserveAspectRatio="none" aria-hidden="true">
      <defs>
        <linearGradient id="band-accent" x1="0" x2="1" y1="0" y2="0">
          <stop offset="0" stop-color="var(--accent-deep)"/>
          <stop offset="1" stop-color="var(--accent)"/>
        </linearGradient>
      </defs>
      <rect x="0" y="0" width="461" height="11" fill="#000"/>
      <polygon points="303,0 461,0 461,11 300,11" fill="url(#band-accent)"/>
      <polygon points="299,0 301,0 298,11 296,11" fill="#fff"/>
    </svg>
  </section>

  <section class="card card-back">
    <div class="back-brand">
      <span class="brand-dot"></span>
      <span class="brand-name">Ridgeline Journeys</span>
    </div>
    <div class="back-url">www.ridgelinejourneys.com.au</div>
  </section>
</body>
</html>
```